Banner Pop Up Opt In Form REDESIGNS - SLEEK BLACK LOOK

Please redesign banners attached.

I am looking for a very sleek look....I do not like this collage of images on these current designs. Please keep all content same but use images that pop.

I have an acccount at www.pixvane-example.com or you can use your own images.

I like black background for somereason because it looks very sleek....but these designs should pop , build trust and credibility and have easy opt in form....SLEEK AND MODERN LOOK is what im looking for....

Target Market(s)

Consumers on websites

Requirements
Must have
• Please redesign banners attached.

Nice to have

Should not have

```html
<!DOCTYPE html>
<html lang="en">
<head>
<meta charset="utf-8">
<title>Newsletter Offer Pop Up</title>
<link rel="stylesheet" href="https://fonts.googleapis.com/css2?family=Open+Sans:wght@300;400;600;700&display=swap">
<style>
  :root {
    --panel: #222222;
    --field: #4a4a4a;
    --field-text: #c9c9c9;
    --button: #000000;
    --button-text: #a9a9a9;
    --gold: #94692b;
    --white: #ffffff;
    --muted: #bdbdbd;
    --sky: #8ec9dc;
    --lagoon: #2fa9a8;
    --deep-sea: #1d6f78;
  }
  * { box-sizing: border-box; margin: 0; padding: 0; }
  html, body { width: 1200px; height: 1032px; overflow: hidden; background: var(--panel); }
  body { font-family: "Open Sans", Arial, sans-serif; }
  .popup { position: relative; width: 1200px; height: 1032px; background: var(--panel); }

  .offer-panel { position: absolute; left: 0; top: 0; width: 718px; height: 1032px; }
  .accent-bar { position: absolute; left: 186px; width: 338px; height: 14px; background: var(--gold); }
  .accent-bar.top { top: 0; }
  .accent-bar.bottom { bottom: 0; }

  .headline {
    position: absolute; top: 84px; left: 0; width: 718px; text-align: center;
    color: var(--white); font-weight: 300; font-size: 66px; line-height: 80px; letter-spacing: 1px;
  }
  .intro {
    position: absolute; top: 326px; left: 0; width: 718px; text-align: center;
    color: var(--muted); font-weight: 600; font-size: 28px; line-height: 37px; letter-spacing: 1px;
    text-transform: uppercase;
  }
  .reward {
    position: absolute; top: 494px; left: 0; width: 718px; text-align: center;
    color: var(--white); font-weight: 700; font-size: 33px; letter-spacing: 1px;
  }

  .signup-form { position: absolute; left: 68px; top: 631px; width: 577px; }
  .field {
    display: block; width: 100%; height: 85px; margin-bottom: 8px;
    background: var(--field); padding: 0 28px;
    color: var(--field-text); font-size: 30px; font-weight: 400; line-height: 85px;
  }
  .submit-button {
    display: block; width: 100%; height: 86px; background: var(--button); border: 0;
    color: var(--button-text); font-family: inherit; font-weight: 700; font-size: 31px; letter-spacing: 1px;
  }

  .visual-column { position: absolute; left: 718px; top: 0; width: 482px; height: 1032px; }
  .hero-photo {
    position: absolute; left: 0; top: 0; width: 482px; height: 818px;
    background:
      linear-gradient(180deg, rgba(34,34,34,0) 70%, rgba(34,34,34,0.35) 100%),
      linear-gradient(180deg, var(--sky) 0%, #bfe3ea 30%, var(--lagoon) 55%, var(--deep-sea) 100%);
  }
  .redeem-note {
    position: absolute; left: 0; top: 818px; width: 482px; height: 214px; background: var(--gold);
    color: var(--white); font-size: 20px; line-height: 28px; text-align: center;
    padding-top: 56px;
  }
</style>
</head>
<body>
<div class="popup">
  <section class="offer-panel">
    <div class="accent-bar top"></div>
    <h1 class="headline">WANT A<br>GREAT OFFER?</h1>
    <p class="intro">Subscribe to our<br>newsletter and<br>receive a complimentary</p>
    <p class="reward">$300 RESTAURANT CERTIFICATE</p>
    <form class="signup-form">
      <div class="field">Name</div>
      <div class="field">Email</div>
      <div class="field">Phone</div>
      <button class="submit-button" type="button">SUBMIT</button>
    </form>
    <div class="accent-bar bottom"></div>
  </section>

  <aside class="visual-column">
    <div class="hero-photo" role="img" aria-label="Single full-height photo of a paddle boarder gliding over a clear turquoise tropical lagoon"></div>
    <p class="redeem-note">We will send an email<br>and text message with the offer<br>and instructions on how to redeem.</p>
  </aside>
</div>
</body>
</html>
```